Natural Light/Organic/Documentary Photography Business

I like a simple, approachable, feminine, earthy/organic feel. Earth/neutral tones, nothing too loud or obnoxious. I like the watercolor look. I don't want anything too trendy or something I'll get tired of after a couple months. As far as colors, I am much more a fan of cream/taupe/blue/green...not a fan of pink or purple at all.

Target Market(s)

Weddings & Families

Industry/Entity Type

Wedding Photography

Contact Information for Business Card

website, email, phone number

Font styles to use
Other font styles liked:
• Horizontes, Gotham

Colors

Designer to choose colors to be used in the design.

Requirements
Must have
• Website: www.mirelhatchway.com
• Phone: 418.629.5073
• Email: mirel@mirelhatchway.com
Nice to have
• I like the watercolor look but its not necessary. I like simple/earthy tones. Nothing too loud or distracting. Simple & feminine without being too girly. I like an approachable/soft feel.
• Instagram: www.instagram.com/mirelhatchwayphotography/
Should not have
• NO loud colors or design or pattern. I do not want a photo of a camera or lens or anything cheesy like that.

```html
<!DOCTYPE html>
<html lang="en">
<head>
<meta charset="utf-8">
<title>Mirel Hatchway Photography – Business Card</title>
<link rel="stylesheet" href="https://fonts.googleapis.com/css2?family=Source+Sans+3:wght@400;600&display=swap">
<style>
  :root {
    --backdrop: #ececec;
    --card-white: #ffffff;
    --taupe: #8f8077;
    --ink: #4f4a47;
    --on-taupe: #ffffff;
  }
  * { margin: 0; padding: 0; box-sizing: border-box; }
  html, body {
    width: 1200px;
    height: 799px;
    overflow: hidden;
    background: var(--backdrop);
    font-family: "Source Sans 3", sans-serif;
  }
  .canvas { position: relative; width: 1200px; height: 799px; }
  .card {
    position: absolute;
    left: 313px;
    width: 583px;
    height: 333px;
  }
  .card--front { top: 51px; background: var(--card-white); }
  .card--back { top: 413px; background: var(--taupe); }

  .contact-list { position: absolute; left: 0; top: 0; list-style: none; }
  .contact-row {
    position: absolute;
    left: 48px;
    display: flex;
    align-items: center;
    white-space: nowrap;
    transform: translateY(-50%);
  }
  .contact-icon {
    width: 14px; height: 14px;
    margin-right: 23px;
    fill: var(--taupe);
    flex: none;
  }
  .contact-text { font-size: 15.5px; color: var(--ink); }
  .contact-row--name .contact-text {
    font-size: 21px; font-weight: 600; color: var(--taupe);
  }
  .row-name { top: 72px; }
  .row-phone { top: 125px; }
  .row-email { top: 176px; }
  .row-web { top: 227px; }
  .row-social { top: 278px; }

  .brand-name {
    position: absolute;
    right: 44px;
    top: 260px;
    font-size: 21px;
    font-weight: 400;
    color: var(--taupe);
    letter-spacing: 0.5px;
  }
  .brand-name--back {
    top: auto;
    right: 40px;
    bottom: 40px;
    font-size: 18px;
    color: var(--on-taupe);
  }
</style>
</head>
<body>
<main class="canvas">
  <section class="card card--front">
    <ul class="contact-list">
      <li class="contact-row contact-row--name row-name">
        <svg class="contact-icon" viewBox="0 0 14 14" aria-hidden="true"><circle cx="7" cy="4" r="3.2"/><path d="M1 14c0-4 2.5-6 6-6s6 2 6 6z"/></svg>
        <span class="contact-text">Mirel Hatchway</span>
      </li>
      <li class="contact-row row-phone">
        <svg class="contact-icon" viewBox="0 0 14 14" aria-hidden="true"><path d="M1 4.5c0-2 2.5-3 6-3s6 1 6 3v1.5h-3V4.5H4V6H1z"/><path d="M3 6.5h8l1.5 6.5h-11z"/></svg>
        <span class="contact-text">418.629.5073</span>
      </li>
      <li class="contact-row row-email">
        <svg class="contact-icon" viewBox="0 0 14 14" aria-hidden="true"><path d="M1 3h12v1.2L7 8 1 4.2z"/><path d="M1 5.6l6 3.8 6-3.8V11H1z"/></svg>
        <span class="contact-text">mirel@mirelhatchway.com</span>
      </li>
      <li class="contact-row row-web">
        <svg class="contact-icon" viewBox="0 0 14 14" aria-hidden="true"><circle cx="7" cy="7" r="6"/><path d="M4 4c1 0 2 1 1.5 2S3.5 7 4 9" stroke="#fff" stroke-width="1" fill="none"/></svg>
        <span class="contact-text">www.mirelhatchway.com</span>
      </li>
      <li class="contact-row row-social">
        <svg class="contact-icon" viewBox="0 0 14 14" aria-hidden="true"><rect x="2" y="2" width="10" height="10"/></svg>
        <span class="contact-text">mirelhatchwayphotography</span>
      </li>
    </ul>
    <p class="brand-name">Mirel Hatchway</p>
  </section>

  <section class="card card--back">
    <p class="brand-name brand-name--back">Mirel Hatchway</p>
  </section>
</main>
</body>
</html>
```